Stationary design for boutique production house

We need a stationary design for our production house, 'Lorno Productions' based in Singapore. We produce microfilms as well as podcasts, talkshows and events. Our logo is a stylized icon of our director, who is also the executive producer and host of our programs, Lorno. Our main company colors are Red, Black and white. We would like a clean, minimalist design incorporating our existing company logo that conveys a sense of urbanism and elegance.

Logo and font files are attached. f

Target Market(s)

We focus on lifestyle media rather than entertainment.

Industry/Entity Type

Boutique

Font styles to use
Serif
Sans Serif

Colors
ec1f27
ffffff
000000

Requirements
Must have
• Our company logo and at least one of our company colors.
Nice to have
• Our address and contact information.
Should not have
• Changes made to the company logo (using only certain parts of it is fine though)

```html
<!DOCTYPE html>
<html lang="en">
<head>
<meta charset="utf-8">
<title>Lorno Productions – Business Card</title>
<link href="https://fonts.googleapis.com/css2?family=Didact+Gothic&display=swap" rel="stylesheet">
<style>
  :root {
    --red: #ec1f27;
    --black: #000000;
    --ink: #1d1d1d;
    --grey: #5a5a5a;
    --white: #ffffff;
    --card-dark: #1b1b1b;
    --stage: #3a3a3a;
  }
  * { box-sizing: border-box; margin: 0; padding: 0; }
  html, body { width: 1200px; height: 768px; overflow: hidden; }
  body {
    background: var(--stage);
    font-family: "Didact Gothic", sans-serif;
    display: flex;
    align-items: center;
    justify-content: center;
    gap: 40px;
  }
  .card {
    width: 540px;
    height: 310px;
    position: relative;
    overflow: hidden;
  }
  /* Back side */
  .card-back { background: var(--black); }
  .back-pattern {
    position: absolute; inset: 0;
    background: linear-gradient(135deg, #262626 0%, var(--card-dark) 60%, #121212 100%);
  }
  .back-brand {
    position: absolute; right: 34px; bottom: 30px;
    text-align: right; color: var(--white);
  }
  .back-brand .brand-name {
    font-size: 22px; letter-spacing: 2px; text-transform: uppercase;
    display: flex; align-items: center; justify-content: flex-end; gap: 10px;
  }
  .back-brand .brand-dot { width: 10px; height: 10px; border-radius: 50%; background: var(--red); }
  .back-brand .back-web { font-size: 13px; margin-top: 8px; letter-spacing: 0.5px; }

  /* Front side */
  .card-front { background: var(--white); padding: 34px 0 0 40px; }
  .contact-name { font-size: 21px; color: var(--ink); letter-spacing: 1px; text-transform: uppercase; }
  .contact-role { font-size: 15px; color: var(--red); letter-spacing: 0.5px; margin-top: 2px; }
  .contact-email { font-size: 15px; color: var(--grey); margin-top: 2px; }
  .divider {
    width: 200px; border: none;
    border-top: 2px dotted var(--red);
    margin: 12px 0 12px;
  }
  .contact-lines p { font-size: 14px; color: var(--grey); line-height: 1.35; }
  .phone-list { list-style: none; }
  .phone-list li {
    display: flex; align-items: center; gap: 8px;
    font-size: 14px; color: var(--grey); line-height: 1.4;
  }
  .phone-list svg { width: 13px; height: 13px; fill: var(--ink); }
  .front-brand {
    position: absolute; right: 36px; top: 130px;
    display: flex; flex-direction: column; align-items: center; gap: 14px;
  }
  .front-brand .brand-dot { width: 16px; height: 16px; border-radius: 50%; background: var(--red); }
  .front-brand .brand-name {
    font-size: 22px; color: var(--ink); letter-spacing: 2px; text-transform: uppercase;
  }
</style>
</head>
<body>

  <section class="card card-back">
    <div class="back-pattern" role="img" aria-label="Faint repeating brand pattern on black"></div>
    <div class="back-brand">
      <div class="brand-name">Lorno Productions<span class="brand-dot"></span></div>
      <div class="back-web">www.lornoprod.com</div>
    </div>
  </section>

  <section class="card card-front">
    <h1 class="contact-name">Mara Velde</h1>
    <p class="contact-role">CEO/FOUNDER</p>
    <p class="contact-email">hello@lornoprod.com</p>
    <hr class="divider">
    <div class="contact-lines">
      <p>42 Keong Saik Road</p>
      <p>Singapore 089143</p>
      <p>www.lornoprod.com</p>
    </div>
    <hr class="divider">
    <ul class="phone-list">
      <li>
        <svg viewBox="0 0 16 16" aria-label="Phone"><path d="M3.5 1l2.5 3-1.5 2c1 2 3 4 5 5l2-1.5 3 2.5-1.5 2.5C7 14 2 9 1 2.5z"/></svg>
        612 555 0184
      </li>
      <li>
        <svg viewBox="0 0 16 16" aria-label="Mobile"><path d="M4 0h8v16H4zM5.5 2v10h5V2zM7 13.3h2v1.4H7z" fill-rule="evenodd"/></svg>
        612 555 0147
      </li>
      <li>
        <svg viewBox="0 0 16 16" aria-label="Fax"><path d="M4 1h8v4H4zM1 6h14v7h-2v2H3v-2H1zM5 11v2h6v-2z" fill-rule="evenodd"/></svg>
        612 555 0199
      </li>
    </ul>
    <div class="front-brand">
      <span class="brand-dot"></span>
      <div class="brand-name">Lorno Productions</div>
    </div>
  </section>

</body>
</html>
```